HOT TUB - SPAS service needs an business card

I need an business for my company who his specialise in a maintenance,water treatment and cleaning of Hot Tub - Spas for commercial and residential customers. The company operate mainly in the ski resort of Chamonix, Megève and St Gervais. The final product should communicate pure water, cleanest and professional for luxury property's.
I have upload a logo but any improvement on it is welcome.(color,size, details etc..) or any other idea. Thank you
Company Name: 58 BAINS
My name: Lucien Marchetti
Email: lucimarch@examplemail.net
Tel: +33 (0)6 71 58 29 64
Description to be on the card in french(first langage) and in English:
- Spas service
- Entretien, traitement eau, nettoyage.
- Maintenance, water treatment, cleaning.
Industry/Entity Type
Residential
Colors
Designer to choose colors to be used in the design.
Look and feel
Each slider illustrates characteristics of the customer's brand and the style your logo design should communicate.

```html
<!DOCTYPE html>
<html lang="fr">
<head>
<meta charset="utf-8">
<title>58 BAINS – Business Card</title>
<link rel="stylesheet" href="https://fonts.googleapis.com/css2?family=Open+Sans:wght@400;600;700&display=swap">
<style>
  :root {
    --page-bg: #eef1f4;
    --front-blue: #1fa3f6;
    --back-blue: #0c74d7;
    --wave-pale: #a9dcff;
    --wave-mid: #3aaeff;
    --wave-deep: #0b6fd2;
    --ink-white: #ffffff;
    --radius: 36px;
  }
  * { box-sizing: border-box; margin: 0; padding: 0; }
  html, body {
    width: 1200px;
    height: 1121px;
    overflow: hidden;
    background: var(--page-bg);
    font-family: "Open Sans", Arial, sans-serif;
    color: var(--ink-white);
  }
  .canvas { position: relative; width: 1200px; height: 1121px; }

  .card {
    position: absolute;
    width: 848px;
    height: 485px;
    border-radius: var(--radius);
    overflow: hidden;
  }
  .card--front { left: 39px; top: 54px; background: var(--front-blue); }
  .card--back  { left: 309px; top: 581px; background: var(--back-blue); }

  .brand-mark {
    position: absolute;
    left: 0; right: 0;
    text-align: center;
    font-weight: 600;
    font-size: 56px;
    letter-spacing: 4px;
    line-height: 1;
  }
  .card--front .brand-mark { top: 70px; }
  .card--back .brand-mark { top: 150px; left: 0; }

  .company-name {
    position: absolute;
    left: 0; right: 0; top: 192px;
    text-align: center;
    font-weight: 600;
    font-size: 40px;
    line-height: 1;
  }
  .contact {
    position: absolute;
    left: 0; right: 0; top: 272px;
    text-align: center;
    font-size: 25px;
    line-height: 40px;
  }
  .contact-line { display: flex; justify-content: center; align-items: center; gap: 10px; }
  .contact-line svg { width: 24px; height: 24px; }

  .wave { position: absolute; left: 0; top: 0; width: 848px; height: 485px; }

  .owner-name {
    position: absolute;
    left: 0; width: 540px; top: 444px;
    text-align: center;
    font-weight: 700;
    font-size: 28px;
    line-height: 1;
  }

  .services-title {
    position: absolute;
    left: 0; right: 0; top: 338px;
    text-align: center;
    font-weight: 600;
    font-size: 29px;
    line-height: 1;
  }
  .services-list {
    position: absolute;
    left: 0; right: 0; top: 386px;
    text-align: center;
    font-size: 29px;
    line-height: 40px;
    list-style: none;
  }
</style>
</head>
<body>
<main class="canvas">

  <section class="card card--front" aria-label="Recto de la carte">
    <svg class="wave" viewBox="0 0 848 485" aria-hidden="true">
      <path d="M0 390 C170 360 330 370 470 390 C620 410 740 380 848 350 L848 485 L0 485 Z" fill="var(--wave-pale)"/>
      <path d="M0 425 C180 395 330 405 480 415 C640 425 760 400 848 378 L848 485 L0 485 Z" fill="var(--wave-mid)"/>
      <path d="M0 440 C170 420 330 428 520 440 C660 446 770 425 848 405 L848 485 L0 485 Z" fill="var(--wave-deep)"/>
    </svg>

    <div class="brand-mark">58 BAINS</div>
    <h1 class="company-name">58 BAINS</h1>

    <div class="contact">
      <p class="contact-line">
        <svg viewBox="0 0 24 24" aria-hidden="true"><circle cx="12" cy="12" r="10" fill="none" stroke="#fff" stroke-width="1.6"/><path d="M8.5 6.5l2 2-1.2 1.6c.8 1.7 2 2.9 3.6 3.7l1.6-1.2 2 2-1.4 1.8c-3.6-.6-7.3-4.3-7.9-7.9z" fill="#fff"/></svg>
        <span>+33 (0)6 71 58 29 64</span>
      </p>
      <p class="contact-line">
        <svg viewBox="0 0 24 24" aria-hidden="true"><path d="M2 9l10-6 10 6v11H2z" fill="#fff"/><path d="M2 9l10 7 10-7" fill="none" stroke="var(--front-blue)" stroke-width="1.6"/></svg>
        <span>lucimarch@examplemail.net</span>
      </p>
    </div>

    <p class="owner-name">Lucien Marchetti</p>
  </section>

  <section class="card card--back" aria-label="Verso de la carte">
    <div class="brand-mark">58 BAINS</div>
    <h2 class="services-title">SPAS SERVICES</h2>
    <ul class="services-list">
      <li>•Entretien &nbsp;•traitement eau &nbsp;•nettoyage</li>
      <li>•Maintenance &nbsp;•water treatment &nbsp;•cleaning.</li>
    </ul>
  </section>

</main>
</body>
</html>
```